Business Card for a New Zealand IT Startup

I need a business card for VELTA Holdings. We are a young startup based in New Zealand working in internet marketing and web development. The design should have some element connected to New Zealand, such as wave, koru or silver fern, just don't use a kiwi bird.

```html
<!DOCTYPE html>
<html lang="en">
<head>
<meta charset="utf-8">
<title>VELTA Holdings Business Card</title>
<link rel="stylesheet" href="https://fonts.googleapis.com/css2?family=Open+Sans:wght@400;600;700&display=swap">
<style>
  :root {
    --backdrop: #3a3a3c;
    --card: #1e1f22;
    --brand-blue: #1b7fd0;
    --brand-orange: #f26522;
    --ink-light: #f2f2f2;
  }
  * { margin: 0; padding: 0; box-sizing: border-box; }
  html, body { width: 799px; height: 1200px; overflow: hidden; }
  body {
    background: var(--backdrop);
    font-family: "Open Sans", Arial, sans-serif;
    position: relative;
  }
  .card {
    position: absolute;
    left: 90px;
    width: 620px;
    height: 354px;
    background: var(--card);
    border-radius: 22px;
    box-shadow: 0 14px 30px rgba(0,0,0,.45);
    overflow: hidden;
  }
  .card--front { top: 110px; }
  .card--back { top: 700px; }

  .wordmark {
    font-weight: 700;
    color: var(--brand-blue);
    display: flex;
    align-items: center;
    gap: 12px;
    white-space: nowrap;
  }
  .wordmark__dot {
    width: 18px; height: 18px;
    background: var(--brand-orange);
    border-radius: 50%;
    flex: none;
  }
  .card--front .wordmark {
    position: absolute;
    top: 110px; left: 0; right: 0;
    justify-content: center;
    font-size: 50px;
    letter-spacing: 1px;
  }
  .site-line {
    position: absolute;
    top: 236px; left: 0; right: 0;
    display: flex; align-items: center; justify-content: center;
    gap: 26px;
  }
  .site-line__rule {
    width: 56px; height: 3px; background: var(--brand-blue);
  }
  .site-line__url {
    color: var(--ink-light);
    font-size: 17px;
  }
  .site-line__url .accent { color: var(--brand-orange); }

  .wave-band {
    position: absolute;
    bottom: 0;
    pointer-events: none;
  }
  .card--front .wave-band { left: 0; width: 620px; height: 64px; }
  .card--back .wave-band { right: 0; width: 230px; height: 70px; }
  .wave-band path { fill: none; stroke-linecap: round; }
  .wave-band .wave--blue { stroke: var(--brand-blue); stroke-width: 3; }
  .wave-band .wave--orange { stroke: var(--brand-orange); stroke-width: 2; }

  .edge-curve {
    position: absolute;
    top: 18px; left: 0;
    width: 14px; height: 60px;
  }
  .edge-curve path { fill: none; stroke: var(--brand-orange); stroke-width: 3; }

  .holder {
    position: absolute; top: 30px; left: 34px;
  }
  .holder__name {
    color: var(--brand-blue);
    font-weight: 700;
    font-size: 21px;
    line-height: 1.1;
  }
  .holder__title {
    color: var(--ink-light);
    font-size: 12px;
    margin-top: 2px;
  }
  .card--back .wordmark {
    position: absolute;
    top: 92px; right: 36px;
    font-size: 34px;
  }
  .card--back .wordmark__dot { width: 13px; height: 13px; }

  .contact {
    position: absolute;
    left: 34px; bottom: 40px;
    list-style: none;
    color: var(--ink-light);
    font-size: 14px;
    line-height: 1.55;
  }
  .contact li { display: flex; align-items: center; gap: 10px; }
  .contact svg { width: 13px; height: 13px; fill: var(--brand-orange); flex: none; }
  .contact__address { font-size: 15px; margin-top: 2px; }
</style>
</head>
<body>
  <section class="card card--front" aria-label="Card front">
    <div class="wordmark"><span class="wordmark__dot"></span>VELTA Holdings</div>
    <div class="site-line">
      <span class="site-line__rule"></span>
      <span class="site-line__url">www.<span class="accent">veltaholdings</span>.com</span>
      <span class="site-line__rule"></span>
    </div>
    <svg class="wave-band" viewBox="0 0 620 64" aria-hidden="true">
      <path class="wave--blue" d="M0 40 C60 20 120 20 180 40 S300 60 360 40 S480 20 540 40 S600 52 620 46"/>
      <path class="wave--orange" d="M0 54 C60 36 120 36 180 54 S300 70 360 54 S480 36 540 54 S600 64 620 60"/>
    </svg>
  </section>

  <section class="card card--back" aria-label="Card back">
    <svg class="edge-curve" viewBox="0 0 14 60" aria-hidden="true">
      <path d="M0 2 C12 18 12 42 0 58"/>
    </svg>
    <div class="holder">
      <p class="holder__name">Aroha Reid Walker</p>
      <p class="holder__title">Managing Director</p>
    </div>
    <div class="wordmark"><span class="wordmark__dot"></span>VELTA Holdings</div>
    <ul class="contact">
      <li>
        <svg viewBox="0 0 24 24" aria-hidden="true"><path d="M6.6 10.8a15.2 15.2 0 0 0 6.6 6.6l2.2-2.2a1 1 0 0 1 1-.25 11.4 11.4 0 0 0 3.6.57 1 1 0 0 1 1 1V20a1 1 0 0 1-1 1A17 17 0 0 1 3 4a1 1 0 0 1 1-1h3.5a1 1 0 0 1 1 1c0 1.25.2 2.45.57 3.57a1 1 0 0 1-.25 1z"/></svg>
        555-0142-318
      </li>
      <li>
        <svg viewBox="0 0 24 24" aria-hidden="true"><path d="M2 5h20v14H2z M4 7v.5l8 5 8-5V7l-8 5z" fill-rule="evenodd"/></svg>
        hello@veltaholdings.com
      </li>
      <li>
        <svg viewBox="0 0 24 24" aria-hidden="true"><path d="M12 2a10 10 0 1 0 0 20 10 10 0 0 0 0-20zm0 2c.9 0 2.2 2 2.7 5H9.3C9.8 6 11.1 4 12 4zM4.3 11h3a19 19 0 0 0 0 2h-3a8 8 0 0 1 0-2zm5 0h5.4a17 17 0 0 1 0 2H9.3a17 17 0 0 1 0-2zm7.4 0h3a8 8 0 0 1 0 2h-3a19 19 0 0 0 0-2zM12 20c-.9 0-2.2-2-2.7-5h5.4c-.5 3-1.8 5-2.7 5z"/></svg>
        www.veltaholdings.com
      </li>
      <li class="contact__address">18 Harbour Lane, Ponsonby, Auckland, NZ 1011</li>
    </ul>
    <svg class="wave-band" viewBox="0 0 230 70" aria-hidden="true">
      <path class="wave--blue" d="M10 46 C50 26 90 26 130 46 S200 62 230 44"/>
      <path class="wave--orange" d="M10 60 C50 42 90 42 130 60 S200 72 230 58"/>
    </svg>
  </section>
</body>
</html>
```